Vosley Insurance Stationery Design Project

We need a stationery design for business cards, letterhead and envelopes.

Please refer to attached brief for further information.

Industry/Entity Type

Business

```html
<!DOCTYPE html>
<html lang="en">
<head>
<meta charset="utf-8">
<title>Vosley Insurance – Business Card</title>
<link href="https://fonts.googleapis.com/css2?family=Source+Sans+3:wght@400;600;700&display=swap" rel="stylesheet">
<style>
  :root {
    --stage: #a9832a;
    --card-white: #ffffff;
    --card-grey: #cccccc;
    --accent-grey: #c8c8c8;
    --orange: #ff7120;
    --text-dark: #1c1c1c;
    --text-grey: #8a8a8a;
    --logo-grey: #b9b9b9;
  }
  * { margin: 0; padding: 0; box-sizing: border-box; }
  html, body { width: 1200px; height: 686px; overflow: hidden; }
  body {
    background: var(--stage);
    font-family: "Source Sans 3", Arial, sans-serif;
    position: relative;
  }
  .card {
    position: absolute;
    width: 523px;
    height: 298px;
    box-shadow: 1px 2px 3px rgba(0,0,0,0.45);
  }
  .card-front { left: 64px; top: 129px; background: var(--card-white); }
  .card-back { left: 611px; top: 298px; background: var(--card-grey); }

  .band { position: absolute; }
  .band-top-orange { left: 178px; top: 0; width: 321px; height: 9px; background: var(--orange); }
  .band-top-grey { left: 459px; top: 0; width: 64px; height: 20px; background: var(--accent-grey); }
  .band-side-grey { left: 0; top: 238px; width: 21px; height: 60px; background: var(--accent-grey); }
  .band-side-orange { left: 0; top: 214px; width: 9px; height: 67px; background: var(--orange); }

  .brand { position: absolute; display: flex; align-items: center; gap: 10px; }
  .brand-dot { border-radius: 50%; background: var(--orange); flex: none; }
  .brand-name { font-weight: 600; line-height: 1; white-space: nowrap; }

  .card-front .brand { left: 43px; top: 58px; }
  .card-front .brand-dot { width: 17px; height: 17px; }
  .card-front .brand-name { font-size: 31px; color: var(--logo-grey); }

  .tagline {
    position: absolute; left: 45px; top: 139px;
    font-size: 11.5px; font-weight: 600; color: var(--logo-grey);
  }
  .disclosure {
    position: absolute; left: 45px; top: 168px;
    font-size: 10.7px; line-height: 16.3px; color: var(--orange);
  }

  .contact {
    position: absolute; right: 41px; top: 77px; text-align: right;
    color: var(--text-dark);
  }
  .contact-name { font-size: 15px; font-weight: 700; color: var(--orange); line-height: 18px; }
  .contact-role { font-size: 12px; font-weight: 600; color: #6e6e6e; line-height: 16px; margin-bottom: 7px; }
  .contact-address { font-size: 11.5px; line-height: 16.3px; margin-bottom: 6px; }
  .contact-lines { font-size: 11.5px; line-height: 18px; }
  .contact-lines b { color: var(--orange); font-weight: 700; }

  .card-back .brand { left: 86px; top: 150px; gap: 14px; }
  .card-back .brand-dot { width: 27px; height: 27px; }
  .card-back .brand-name { font-size: 48px; color: var(--orange); }
  .web {
    position: absolute; left: 86px; width: 337px; top: 200px; text-align: right;
    font-size: 11.5px; font-weight: 700; letter-spacing: 1.4px; color: var(--text-dark);
  }
  .web span { color: var(--orange); }
</style>
</head>
<body>
  <section class="card card-front">
    <div class="band band-top-orange"></div>
    <div class="band band-top-grey"></div>
    <div class="band band-side-grey"></div>
    <div class="band band-side-orange"></div>

    <div class="brand">
      <span class="brand-dot"></span>
      <span class="brand-name">Vosley Insurance</span>
    </div>

    <p class="tagline">Business and Life Insurance Brokers and Advisers</p>
    <p class="disclosure">
      Authorised Representative No. 482193<br>
      Broker Network Australia Pty Limited AFSL 310274<br>
      Broker Network Financial Services Pty Ltd<br>
      and its advisers are members of Harlow Financial<br>
      Advisers and Authorised Representatives<br>
      of Kestrel Advice group Pty Ltd AFSL 265031
    </p>

    <div class="contact">
      <p class="contact-name">Mark Vosley</p>
      <p class="contact-role">Director</p>
      <p class="contact-address">
        Level 4, 18 Carran St<br>
        Eastbridge NSW 2061<br>
        PO Box 418<br>
        Eastbridge NSW 2058
      </p>
      <p class="contact-lines">
        <b>T</b> : (02) 5550 1290<br>
        <b>F</b> : (02) 5550 1291<br>
        <b>M</b> : 0400 555 812<br>
        <b>E</b> : mvosley@broknet.example
      </p>
    </div>
  </section>

  <section class="card card-back">
    <div class="brand">
      <span class="brand-dot"></span>
      <span class="brand-name">Vosley Insurance</span>
    </div>
    <p class="web">www.<span>vosleyinsurance</span>.example</p>
  </section>
</body>
</html>
```